Allied Health team of Physiotherapists & Occupational Therapists seek a business card design

We have our new logo, we now need our new business cards and stationary. Tidewell: Oedema & Family Clinic is seeking a generic card design to represent our whole team and individual cards for each therapist that incorporates our new logo to communicate our holistic approach that is calming, nuturing, supportive and welcoming.
Our Physiotherapists and Occupational Therapists assess, treat and provide education for people who are at risk of or who have lymphoedema. This is often as a result of treatment for cancer. We provide pre-operative and post-operative management and cancer rehabilitation in our Pilates studio. Our team also consists of Physiotherapists who have a strong interest in pelvic floor and continence management for both men and women.

Target Market(s)

Mainly women health conscious

Industry/Entity Type

Allied Health: Physiotherapy / Occupational Therapy

Contact Information for Business Card

Address: 14 Gallivant Ave Harbourne 3921 Phone: 84316570 fax: 8431 6578 Email: info@tidewellcareservices.com.au Website: tidewellcareservices.com.au Facebook address: facebook.com/TidewellOedemaAndFamilyCareClinic. Room to write appointments. Individual cards need to have name, office email and individual email and professional details

Requirements
Must have
• Logo as per uploaded documents

```html
<!DOCTYPE html>
<html lang="en">
<head>
<meta charset="utf-8">
<title>Tidewell Business Card</title>
<link href="https://fonts.googleapis.com/css2?family=Philosopher:wght@700&family=Roboto:ital,wght@0,400;1,400&display=swap" rel="stylesheet">
<style>
  :root {
    --backdrop: #2c2c2c;
    --apricot: #de936d;
    --apricot-deep: #d5865f;
    --cream: #f1e7b4;
    --paper: #efefef;
    --sage: #b9c2b3;
    --ink: #333333;
  }
  html, body {
    margin: 0;
    padding: 0;
    width: 1200px;
    height: 1138px;
    overflow: hidden;
    background: var(--backdrop);
  }
  .canvas {
    position: relative;
    width: 1200px;
    height: 1138px;
  }
  .card {
    position: absolute;
    width: 622px;
    height: 375px;
    border-radius: 16px;
    overflow: hidden;
  }
  .card-front {
    left: 274px;
    top: 186px;
    background: linear-gradient(180deg, var(--apricot-deep), var(--apricot));
  }
  .card-back {
    left: 276px;
    top: 608px;
    width: 618px;
    height: 374px;
    background: var(--paper);
  }
  .brand {
    position: absolute;
    text-align: center;
    font-family: "Philosopher", sans-serif;
    font-weight: 700;
    color: var(--cream);
    line-height: 1.2;
  }
  .card-front .brand {
    left: 0;
    right: 0;
    top: 152px;
    font-size: 30px;
  }
  .card-back .brand {
    left: 0;
    width: 268px;
    top: 158px;
    font-size: 24px;
  }
  .back-shape {
    position: absolute;
    inset: 0;
  }
  .details {
    position: absolute;
    left: 302px;
    top: 76px;
    font-family: "Roboto", sans-serif;
    color: var(--ink);
    font-size: 15px;
    line-height: 21px;
  }
  .person-name {
    margin: 0 0 2px;
    font-family: "Philosopher", sans-serif;
    font-weight: 700;
    font-size: 21px;
    color: var(--apricot-deep);
    line-height: 26px;
  }
  .role {
    margin: 0;
    font-style: italic;
    font-size: 14px;
  }
  .specialty {
    margin: 0;
  }
  .contacts {
    list-style: none;
    margin: 26px 0 0;
    padding: 0;
    font-size: 16px;
  }
  .contacts li {
    display: flex;
    align-items: center;
    height: 26px;
  }
  .contacts svg {
    width: 14px;
    height: 14px;
    margin-right: 12px;
    fill: var(--apricot-deep);
    flex: none;
  }
  .phone-pair span + svg {
    margin-left: 22px;
  }
</style>
</head>
<body>
<div class="canvas">

  <section class="card card-front">
    <div class="brand">Tidewell: Oedema<br>&amp; Family Clinic</div>
  </section>

  <section class="card card-back">
    <svg class="back-shape" viewBox="0 0 618 374" preserveAspectRatio="none" aria-hidden="true">
      <path d="M0 0 H220 Q350 190 244 374 H0 Z" fill="var(--sage)"/>
      <path d="M0 0 H214 Q340 190 234 374 H0 Z" fill="var(--apricot)"/>
    </svg>
    <div class="brand">Tidewell: Oedema<br>&amp; Family Clinic</div>

    <div class="details">
      <h1 class="person-name">Marla Brenton</h1>
      <p class="role">Physiotherapist</p>
      <p class="specialty">Lymphoedema &amp; Oncology Rehabilitation</p>
      <p class="specialty">Continence &amp; Pelvic Floor</p>

      <ul class="contacts">
        <li class="phone-pair">
          <svg viewBox="0 0 16 16"><path d="M2 5c0-2 2-3 6-3s6 1 6 3v1h-3V5H5v1H2zM4 7h8l2 6H2z"/></svg>
          <span>8431 6570</span>
          <svg viewBox="0 0 16 16"><path d="M2 5c0-2 2-3 6-3s6 1 6 3v1h-3V5H5v1H2zM4 7h8l2 6H2z"/></svg>
          <span>8431 6578</span>
        </li>
        <li>
          <svg viewBox="0 0 16 16"><path d="M1 3h14v10H1zM2 4l6 5 6-5v1L8 10 2 5z" fill-rule="evenodd"/></svg>
          <span>info@tidewellcareservices.com.au</span>
        </li>
        <li>
          <svg viewBox="0 0 16 16"><path d="M8 1a7 7 0 1 0 0 14A7 7 0 0 0 8 1zm0 1.5c.9 1 1.5 2.5 1.7 4.5H6.3C6.5 5 7.1 3.5 8 2.5zM2.6 7h2.3c.1-1.7.5-3 1.1-4A5.6 5.6 0 0 0 2.6 7zm0 2A5.6 5.6 0 0 0 6 13c-.6-1-1-2.3-1.1-4zm3.7 0c.2 2 .8 3.5 1.7 4.5.9-1 1.5-2.5 1.7-4.5zm4.8 0c-.1 1.7-.5 3-1.1 4A5.6 5.6 0 0 0 13.4 9zm2.3-2A5.6 5.6 0 0 0 10 3c.6 1 1 2.3 1.1 4z"/></svg>
          <span>www.tidewellcareservices.com.au</span>
        </li>
        <li>
          <svg viewBox="0 0 16 16"><path d="M8 1a5 5 0 0 0-5 5c0 4 5 9 5 9s5-5 5-9a5 5 0 0 0-5-5zm0 3a2 2 0 1 1 0 4 2 2 0 0 1 0-4z" fill-rule="evenodd"/></svg>
          <span>14 Gallivant Ave, Harbourne 3921</span>
        </li>
      </ul>
    </div>
  </section>

</div>
</body>
</html>
```